Corbell Lending Partners - Real estate loans - need a business card with a logo

I need a logo and a business card that looks elegant - that looks as if it is a big stablish corporation - We do real estate loans, my goal is to brand myself with colors black background - gold or silver letters - some combination - Name of the company different color than the rest of the card -

```html
<!DOCTYPE html>
<html lang="en">
<head>
<meta charset="utf-8">
<title>Corbell Lending Partners — Business Card</title>
<link rel="stylesheet" href="https://fonts.googleapis.com/css2?family=Archivo:wght@400;600&display=swap">
<style>
  :root {
    --stage: #3a3a3a;
    --card: #0e0e0f;
    --emboss: #333336;
    --gold: #d4b075;
    --silver: #d9dadc;
  }
  * { margin: 0; padding: 0; box-sizing: border-box; }
  html, body { width: 1200px; height: 900px; overflow: hidden; background: var(--stage); }
  body { font-family: "Archivo", Arial, sans-serif; position: relative; }

  .card {
    position: absolute;
    left: 290px;
    width: 620px;
    height: 354px;
    background: var(--card);
    border-bottom: 4px solid var(--gold);
  }
  .card--front { top: 60px; }
  .card--back { top: 470px; }

  .wordmark {
    display: flex;
    align-items: center;
    gap: 14px;
    font-weight: 600;
    text-transform: uppercase;
    line-height: 1.1;
  }
  .wordmark__mark { width: 20px; height: 20px; flex: none; background: currentColor; }
  .wordmark__main { font-size: 38px; letter-spacing: 4px; }
  .wordmark__sub { font-size: 17px; letter-spacing: 4.2px; }

  .card--front .wordmark {
    position: absolute;
    left: 50%;
    top: 50%;
    transform: translate(-50%, -50%);
    color: var(--emboss);
  }

  .card--back .wordmark {
    position: absolute;
    left: 34px;
    top: 142px;
    color: var(--gold);
  }
  .card--back .wordmark__main { font-size: 34px; letter-spacing: 3.5px; }
  .card--back .wordmark__sub { font-size: 15px; letter-spacing: 3.8px; }

  .divider {
    position: absolute;
    left: 338px;
    top: 92px;
    width: 2px;
    height: 172px;
    background: var(--gold);
  }

  .contact {
    position: absolute;
    left: 362px;
    top: 92px;
    color: var(--silver);
    font-size: 15px;
    line-height: 1.35;
  }
  .contact__person {
    color: var(--gold);
    font-weight: 600;
    font-size: 22px;
    letter-spacing: 1px;
    text-transform: uppercase;
  }
  .contact__role { margin-bottom: 10px; }
  .contact__address { margin-bottom: 8px; }
  .contact__row { display: flex; align-items: center; gap: 8px; }
  .contact__row svg { width: 12px; height: 12px; flex: none; }
</style>
</head>
<body>
  <section class="card card--front" aria-label="Card front">
    <div class="wordmark">
      <span class="wordmark__mark" aria-hidden="true"></span>
      <div>
        <div class="wordmark__main">Corbell</div>
        <div class="wordmark__sub">Lending Partners</div>
      </div>
    </div>
  </section>

  <section class="card card--back" aria-label="Card back">
    <div class="wordmark">
      <span class="wordmark__mark" aria-hidden="true"></span>
      <div>
        <div class="wordmark__main">Corbell</div>
        <div class="wordmark__sub">Lending Partners</div>
      </div>
    </div>
    <div class="divider"></div>
    <div class="contact">
      <div class="contact__person">Daniel Hartwell</div>
      <div class="contact__role">Founder</div>
      <div class="contact__address">418 Alder Court<br>Brightwater, WA 99000</div>
      <div class="contact__row">
        <svg viewBox="0 0 12 12" aria-hidden="true"><path d="M2.5 1 L4.5 1 L5.2 3.6 L4 4.6 Q5 7 7.4 8 L8.4 6.8 L11 7.5 L11 9.5 Q10 11 8.5 11 Q1 9.5 1 3.5 Q1 2 2.5 1 Z" fill="#d4b075"/></svg>
        <span>555 014 2378</span>
      </div>
      <div class="contact__row">
        <svg viewBox="0 0 12 12" aria-hidden="true"><rect x="1" y="2.5" width="10" height="7" fill="none" stroke="#d4b075" stroke-width="1.1"/><path d="M1 2.5 L6 6.5 L11 2.5" fill="none" stroke="#d4b075" stroke-width="1.1"/></svg>
        <span>info@corbelllending.com</span>
      </div>
      <div class="contact__row">
        <svg viewBox="0 0 12 12" aria-hidden="true"><g fill="none" stroke="#d4b075" stroke-width="1"><circle cx="6" cy="6" r="5"/><ellipse cx="6" cy="6" rx="2.2" ry="5"/><path d="M1 6 H11 M2 3.5 H10 M2 8.5 H10"/></g></svg>
        <span>www.corbelllending.com</span>
      </div>
    </div>
  </section>
</body>
</html>
```